Web design required

1-We need a web design for existing company based in New Zealand
2-We build residential house and light commercial
3-We has in-house designer which allow us can provide interior design
4-We modeling project before site construction, which enable both client and construction team to visually analysis whole project,

Target Market(s)

middle class residential house market
Ref: http://www.parvellbuilders.co.nz/

Industry/Entity Type

Construction Company

Number of Pages Required

1 page

Font styles to use
Sans Serif
Other font styles liked:
• Such as : Central Gothic or similar which has more design taste

Colors

Designer to choose colors to be used in the design.

Requirements
Must have
• Front sheet, contact information, sample project

```html
<!DOCTYPE html>
<html lang="en">
<head>
<meta charset="utf-8">
<title>Kestrel Homes</title>
<link href="https://fonts.googleapis.com/css2?family=Montserrat:wght@400;600;700&family=Open+Sans:wght@400;600&display=swap" rel="stylesheet">
<style>
:root{
  --blue:#1b5aa6;
  --blue-dark:#123f78;
  --ink:#2b2b2b;
  --muted:#6f6f6f;
  --grey-bg:#ececec;
  --line:#d6d6d6;
  --footer:#2a2d33;
  --white:#ffffff;
}
*{margin:0;padding:0;box-sizing:border-box}
html,body{width:1200px;height:3102px;overflow:hidden}
body{font-family:"Open Sans",Arial,sans-serif;color:var(--ink);background:var(--white);position:relative}
.heading{font-family:"Montserrat",Arial,sans-serif}
.topbar{height:30px;background:var(--white);display:flex;justify-content:flex-end;align-items:center;gap:10px;padding-right:40px}
.topbar span{background:var(--blue);color:var(--white);font-size:11px;padding:5px 12px;border-radius:2px;display:flex;align-items:center;gap:6px}
.header{height:90px;display:flex;align-items:center;justify-content:space-between;padding:0 40px 0 140px;margin-top:-30px}
.brand{display:flex;align-items:center;gap:10px;font-family:"Montserrat",sans-serif;font-weight:700;font-size:22px;color:var(--blue);letter-spacing:1px}
.brand .dot{width:34px;height:34px;background:var(--blue);border-radius:50%}
.nav{display:flex;gap:34px;font-family:"Montserrat",sans-serif;font-size:13px;font-weight:600;margin-top:40px}
.nav a{color:var(--ink);text-decoration:none;text-transform:uppercase}
.nav a.active{border:2px solid var(--line);border-radius:50%;padding:18px 10px;margin-top:-26px;color:var(--blue)}
.hero{position:absolute;top:120px;left:0;width:1200px;height:460px;background:linear-gradient(180deg,#9fb7c9 0%,#c7d0cf 35%,#8a7b62 60%,#3f5a2e 85%,#2e3f22 100%)}
.hero .arrow{position:absolute;top:180px;width:44px;height:44px;border-radius:50%;background:rgba(255,255,255,.35)}
.hero .arrow.left{left:24px}.hero .arrow.right{right:24px}
.tagline{position:absolute;bottom:10px;left:0;width:1200px;height:48px;background:rgba(20,40,70,.75);color:var(--white);font-family:"Montserrat",sans-serif;font-size:24px;display:flex;align-items:center;justify-content:center}
.about{position:absolute;top:620px;left:140px;width:920px;display:flex;justify-content:space-between}
.about-text{width:600px}
.about-text h2{font-size:30px;font-weight:700;letter-spacing:.5px}
.about-text h2 b{color:var(--blue)}
.rule{display:flex;align-items:center;gap:6px;margin:10px 0 14px}
.rule i{width:22px;height:22px;border-radius:50%;background:var(--line);display:block}
.rule s{width:260px;height:1px;background:var(--line);display:block}
.about-text p{font-size:12.5px;line-height:22px;color:var(--muted)}
.btn{display:inline-block;background:var(--blue);color:var(--white);font-family:"Montserrat",sans-serif;font-size:11px;font-weight:600;padding:8px 14px;margin-top:16px;text-transform:uppercase}
.estimate{width:248px;border:1px solid var(--line)}
.estimate h3{background:#2d2d2d;color:var(--white);font-size:15px;text-align:center;padding:16px 0;font-family:"Montserrat",sans-serif}
.estimate form{padding:16px}
.field{border:1px solid var(--line);height:30px;font-size:11px;color:#999;padding:7px 8px;margin-bottom:10px}
.field.tall{height:46px}
.estimate .submit{background:var(--blue);color:var(--white);text-align:center;font-size:12px;font-weight:600;padding:8px 0}
.services{position:absolute;top:1020px;left:0;width:1200px;height:580px;background:var(--grey-bg)}
.section-title{text-align:center;font-family:"Montserrat",sans-serif;font-size:30px;font-weight:700}
.section-title b{color:var(--blue)}
.center-rule{display:flex;justify-content:center;align-items:center;gap:6px;margin-top:10px}
.center-rule s{width:420px;height:1px;background:#cfcfcf;display:block}
.center-rule i{width:22px;height:22px;border-radius:50%;background:#cfcfcf;display:block}
.services .section-title{padding-top:50px}
.cards{display:flex;justify-content:center;gap:50px;margin-top:22px}
.card{width:430px;height:430px;background:var(--white);border-bottom:4px solid var(--blue);text-align:center;position:relative}
.card .photo{height:210px}
.card .icon{position:absolute;top:172px;left:185px;width:60px;height:60px;border-radius:50%;background:var(--blue);border:4px solid var(--white);display:flex;align-items:center;justify-content:center}
.card h4{margin-top:48px;font-family:"Montserrat",sans-serif;font-size:19px;font-weight:700}
.card p{font-size:12px;line-height:19px;color:var(--muted);padding:8px 70px 0}
.projects{position:absolute;top:1600px;left:0;width:1200px;height:700px}
.projects .section-title{padding-top:110px}
.hexes{position:absolute;top:190px;left:0}
.testimonials{position:absolute;top:2300px;left:0;width:1200px;height:460px;background:#e4e4e4}
.testimonials .section-title{padding-top:60px}
.people{display:flex;justify-content:center;gap:70px;margin-top:32px;position:relative}
.person{text-align:center;font-size:12px;font-weight:600}
.person .avatar{width:90px;height:90px;border-radius:50%;background:linear-gradient(#c9a98c,#7d6552);border:4px solid var(--white);box-shadow:0 0 0 1px var(--line);margin:0 auto 8px}
.t-arrow{position:absolute;top:30px;font-size:26px;color:#999}
.quote{width:900px;margin:28px auto 0;background:var(--white);font-size:12px;line-height:20px;color:var(--muted);padding:18px 26px;text-align:center}
.footer{position:absolute;top:2760px;left:0;width:1200px;height:342px;background:linear-gradient(180deg,#2f343c,#23262c);color:#cfd3d8}
.footer .cols{display:flex;gap:70px;padding:40px 0 0 140px}
.footer h5{font-family:"Montserrat",sans-serif;font-size:13px;color:var(--white);text-transform:uppercase;margin-bottom:14px}
.footer li{list-style:none;font-size:12px;line-height:22px}
.contact-row{display:flex;gap:8px;align-items:center;font-size:12px;line-height:22px}
.map{width:240px;height:140px;background:linear-gradient(135deg,#e7e3d8,#cfd8c9)}
.footer-brand{position:absolute;right:140px;top:70px;text-align:center}
.footer-brand .name{font-family:"Montserrat",sans-serif;font-weight:700;font-size:18px;color:var(--white);letter-spacing:1px}
.social{display:flex;gap:6px;justify-content:center;margin-top:16px}
.social i{width:22px;height:22px;border-radius:50%;background:var(--blue);display:block}
.copyright{position:absolute;bottom:0;left:0;width:1200px;height:40px;background:#1b1d21;font-size:11px;display:flex;align-items:center;justify-content:center;color:#aab}
</style>
</head>
<body>
<div class="topbar">
  <span><svg width="10" height="10" viewBox="0 0 10 10"><path d="M2 1l2 2-1 1a6 6 0 003 3l1-1 2 2-1 1C4 9 1 6 1 2z" fill="#fff"/></svg>0800 555 214</span>
  <span><svg width="12" height="9" viewBox="0 0 12 9"><rect x=".5" y=".5" width="11" height="8" fill="none" stroke="#fff"/><path d="M.5.5l5.5 4 5.5-4" fill="none" stroke="#fff"/></svg>hello@kestrelhomes.co.nz</span>
</div>
<header class="header">
  <div class="brand"><span class="dot"></span>KESTREL HOMES</div>
  <nav class="nav">
    <a class="active" href="#">Home</a><a href="#">About Us</a><a href="#">Services</a><a href="#">Recent Projects</a><a href="#">Contact Us</a>
  </nav>
</header>

<section class="hero" role="img" aria-label="Modern two-storey family home with lit windows at dusk">
  <span class="arrow left"></span><span class="arrow right"></span>
  <div class="tagline">We Build Residential House And Light Commercial</div>
</section>

<section class="about">
  <div class="about-text">
    <h2 class="heading">ABOUT <b>KESTREL HOMES</b></h2>
    <div class="rule"><i></i><s></s></div>
    <p>Kestrel Homes is a New Zealand building company creating quality family homes and light commercial spaces. Our in-house designer helps every client shape the interior to suit the way they live, from layout and finishes to lighting and storage. Before work starts on site we model each project in full, so clients and our construction team can walk through the whole build, spot issues early and make confident decisions together. We keep budgets clear, timelines honest and workmanship to the highest standard, delivering homes that feel right from the first day you move in and for many years to come.</p>
    <span class="btn">Read More</span>
  </div>
  <aside class="estimate">
    <h3>GET A FREE ESTIMATE</h3>
    <form>
      <div class="field">Name</div>
      <div class="field">Email</div>
      <div class="field">Service ▾</div>
      <div class="field tall">Message</div>
      <div class="submit">SUBMIT</div>
    </form>
  </aside>
</section>

<section class="services">
  <h2 class="section-title">OUR <b>SERVICES</b></h2>
  <div class="center-rule"><s></s><i></i><s></s></div>
  <div class="cards">
    <article class="card">
      <div class="photo" role="img" aria-label="Contemporary residential house with garage at twilight" style="background:linear-gradient(180deg,#5d7896,#8d8a82 55%,#4b4d46)"></div>
      <div class="icon"><svg width="28" height="26" viewBox="0 0 28 26"><path d="M14 2L2 12h4v12h16V12h4z" fill="#fff"/></svg></div>
      <h4>RESIDENTIAL SERVICES</h4>
      <p>Custom family homes designed and built around your lifestyle, with interior design support and full 3D modelling before construction.</p>
      <span class="btn">Read More</span>
    </article>
    <article class="card">
      <div class="photo" role="img" aria-label="Glass commercial office towers against a blue sky" style="background:linear-gradient(180deg,#c6dbef,#7ea5cc 60%,#4d6f94)"></div>
      <div class="icon"><svg width="26" height="26" viewBox="0 0 26 26"><path d="M3 24V6h8v18M13 24V2h10v22" fill="#fff"/></svg></div>
      <h4>COMMERCIAL SERVICES</h4>
      <p>Light commercial builds for offices, retail and small workspaces, planned carefully to deliver on time, on budget and to standard.</p>
      <span class="btn">Read More</span>
    </article>
  </div>
</section>

<section class="projects">
  <h2 class="section-title">RECENT <b>PROJECTS</b></h2>
  <div class="center-rule"><s></s><i></i><s></s></div>
  <svg class="hexes" width="1200" height="480" viewBox="0 0 1200 480">
    <defs>
      <linearGradient id="gHouse" x1="0" y1="0" x2="0" y2="1"><stop offset="0" stop-color="#8fb3d6"/><stop offset=".6" stop-color="#b49a7c"/><stop offset="1" stop-color="#5d7a3c"/></linearGradient>
      <linearGradient id="gTower" x1="0" y1="0" x2="0" y2="1"><stop offset="0" stop-color="#d7e6f4"/><stop offset="1" stop-color="#5f86b0"/></linearGradient>
    </defs>
    <g stroke="#1b5aa6" stroke-width="6">
      <polygon role="img" aria-label="Completed brick family home" points="240,30 318,75 318,165 240,210 162,165 162,75" fill="url(#gHouse)"/>
      <polygon role="img" aria-label="Modern glass office building" points="420,30 498,75 498,165 420,210 342,165 342,75" fill="url(#gTower)"/>
      <polygon role="img" aria-label="Suburban two-storey house" points="600,30 678,75 678,165 600,210 522,165 522,75" fill="url(#gHouse)"/>
      <polygon role="img" aria-label="Commercial block with glass facade" points="780,30 858,75 858,165 780,210 702,165 702,75" fill="url(#gTower)"/>
      <polygon role="img" aria-label="Contemporary family home with lawn" points="960,30 1038,75 1038,165 960,210 882,165 882,75" fill="url(#gHouse)"/>
      <polygon role="img" aria-label="Light commercial building exterior" points="360,200 438,245 438,335 360,380 282,335 282,245" fill="url(#gTower)"/>
      <polygon role="img" aria-label="Newly built residential house" points="840,200 918,245 918,335 840,380 762,335 762,245" fill="url(#gHouse)"/>
    </g>
    <circle cx="600" cy="290" r="14" fill="#1b5aa6"/>
    <text x="600" y="330" text-anchor="middle" font-family="Montserrat, sans-serif" font-weight="700" font-size="20" fill="#1b5aa6">KESTREL HOMES</text>
  </svg>
</section>

<section class="testimonials">
  <h2 class="section-title">CLIENT <b>TESTIMONIALS</b></h2>
  <div class="center-rule"><s></s><i></i><s></s></div>
  <div class="people">
    <span class="t-arrow" style="left:250px">‹</span>
    <div class="person"><div class="avatar" role="img" aria-label="Client portrait"></div>Hana Ropata</div>
    <div class="person"><div class="avatar" role="img" aria-label="Client portrait"></div>Liam Carter</div>
    <div class="person"><div class="avatar" role="img" aria-label="Client portrait"></div>Aroha Tane</div>
    <div class="person"><div class="avatar" role="img" aria-label="Client portrait"></div>Sam Whitfield</div>
    <span class="t-arrow" style="right:250px">›</span>
  </div>
  <p class="quote">“From the first design meeting to handover, the team was clear, friendly and organised. Seeing our home modelled before construction began meant we could change the kitchen and living layout early without any stress. The build finished on time, the finish quality is excellent, and we would happily recommend them to anyone planning a new home for their family.”</p>
</section>

<footer class="footer" role="img" aria-label="Dark city skyline behind footer content">
  <div class="cols">
    <div>
      <h5>Quick Links</h5>
      <ul><li>Home</li><li>About Us</li><li>Services</li><li>Recent Projects</li><li>Contact Us</li></ul>
    </div>
    <div>
      <h5>Contact Details</h5>
      <div class="contact-row"><svg width="10" height="14" viewBox="0 0 10 14"><path d="M5 0a5 5 0 00-5 5c0 4 5 9 5 9s5-5 5-9a5 5 0 00-5-5z" fill="#fff"/></svg>Kestrel Homes</div>
      <div class="contact-row" style="padding-left:18px">42 Harbour Road, Auckland</div>
      <div class="contact-row"><svg width="10" height="10" viewBox="0 0 10 10"><path d="M2 1l2 2-1 1a6 6 0 003 3l1-1 2 2-1 1C4 9 1 6 1 2z" fill="#fff"/></svg>0800 555 214</div>
      <div class="contact-row"><svg width="12" height="9" viewBox="0 0 12 9"><rect x=".5" y=".5" width="11" height="8" fill="none" stroke="#fff"/></svg>hello@kestrelhomes.co.nz</div>
    </div>
    <div>
      <h5>Location Map</h5>
      <div class="map" role="img" aria-label="Street map showing office location"></div>
    </div>
  </div>
  <div class="footer-brand">
    <div class="name">KESTREL HOMES</div>
    <div class="social"><i></i><i></i><i></i><i></i></div>
  </div>
  <div class="copyright">Copyright © 2017 KESTREL HOMES. All Rights Reserved.</div>
</footer>
</body>
</html>
```